RESINE DENTAIRE ROSE box for dental resine pink to repair dentures broken

I will need a design for a box of pink dental resin. It is a pink dental resin which is intended for sale to individuals on Brindleway to repair or make small touch-ups or modifications to their dental prostheses. The title RESINE DENTAIRE ROSE must be clearly visible as well as the company logo. .I leave it to your creative mind to make an attractive and highly impactful and clearly visible sales design.
It is also necessary to make it clear to buyers through text or a vector image the purpose of the product: to repair a dental prosthesis.
Faible participation designers
Particulars who have need to repair their dentures

```html
<!DOCTYPE html>
<html lang="fr">
<head>
<meta charset="utf-8">
<title>Résine Rose Dentaire – Laboratoire Calvadent</title>
<link rel="stylesheet" href="https://fonts.googleapis.com/css2?family=Alfa+Slab+One&family=Passion+One:wght@700&family=Roboto+Condensed:wght@400;500&display=swap">
<style>
  :root {
    --paper: #f1f2f3;
    --blush: #efdae1;
    --magenta: #d3165d;
    --green: #2f9a3a;
    --ink: #1e1e1e;
  }
  html, body {
    margin: 0;
    width: 1154px;
    height: 1200px;
    overflow: hidden;
    background: var(--blush);
  }
  .box-front {
    position: relative;
    width: 1154px;
    height: 1200px;
    background: linear-gradient(to bottom, var(--paper) 0 527px, var(--blush) 527px 100%);
    font-family: "Roboto Condensed", sans-serif;
  }
  .brand {
    position: absolute;
    top: 96px;
    left: 0;
    width: 100%;
    display: flex;
    justify-content: center;
    align-items: center;
    gap: 24px;
  }
  .brand-mark {
    width: 86px;
    height: 86px;
    background: var(--green);
  }
  .brand-name {
    color: var(--green);
    font-weight: 500;
    font-size: 58px;
    line-height: 1.05;
    letter-spacing: 1px;
    text-transform: uppercase;
  }
  .brand-since {
    color: var(--green);
    font-weight: 500;
    font-size: 26px;
    line-height: 1.1;
    text-align: center;
    align-self: flex-end;
  }
  .hero {
    position: absolute;
    inset: 0;
  }
  .purpose {
    position: absolute;
    top: 826px;
    left: 0;
    width: 100%;
    margin: 0;
    text-align: center;
    color: var(--ink);
    font-size: 52px;
    line-height: 70px;
    transform: scaleX(0.92);
  }
  .icon-slot {
    position: absolute;
    top: 822px;
    width: 170px;
    height: 170px;
    border-radius: 50%;
    background: linear-gradient(to bottom, #fbeaf0 0 45%, var(--magenta) 45% 100%);
    border: 4px solid var(--magenta);
    box-sizing: border-box;
  }
  .icon-left { left: 104px; }
  .icon-right { left: 868px; }
  .volume {
    position: absolute;
    top: 1118px;
    width: 100%;
    text-align: center;
    font-size: 42px;
    color: var(--ink);
  }
</style>
</head>
<body>
<main class="box-front">
  <header class="brand">
    <div class="brand-mark" aria-hidden="true"></div>
    <div class="brand-name">Laboratoire<br>Calvadent</div>
    <div class="brand-since">Depuis<br>1990</div>
  </header>

  <svg class="hero" width="1154" height="1200" viewBox="0 0 1154 1200">
    <defs>
      <path id="title-arc" d="M 250 440 Q 576 250 910 440"/>
    </defs>
    <rect class="band" x="0" y="527" width="1154" height="111" fill="var(--magenta)"/>
    <ellipse cx="576" cy="581" rx="372" ry="200" fill="var(--blush)"/>
    <ellipse role="img" aria-label="Illustration d'une bouche ouverte avec dents" cx="576" cy="581" rx="352" ry="184" fill="var(--magenta)" stroke="var(--green)" stroke-width="12"/>
    <text font-family="Passion One, sans-serif" font-weight="700" font-size="96" fill="var(--magenta)">
      <textPath href="#title-arc" startOffset="50%" text-anchor="middle">Résine Rose</textPath>
    </text>
    <text x="576" y="632" text-anchor="middle" textLength="620" lengthAdjust="spacingAndGlyphs"
          font-family="Alfa Slab One, serif" font-size="140" fill="var(--paper)"
          stroke="var(--magenta)" stroke-width="3">DENTAIRE</text>
  </svg>

  <div class="icon-slot icon-left" role="img" aria-label="Pictogramme de réparation d'une prothèse dentaire"></div>
  <p class="purpose">Pour la réparation<br>de prothèses dentaires</p>
  <div class="icon-slot icon-right" role="img" aria-label="Pictogramme de prothèse dentaire réparée"></div>

  <div class="volume">100ml</div>
</main>
</body>
</html>
```